Sustainably Transforming Education

Company is education services based. early learning through adult and corporate. Focus is national government policy and program design and delivery alongside a research based and academically grounded set of approaches to planning, evaluation, and change management.I am looking for an innovative design position that aligns with the global agendas for innovation, creativity and collaboration at international and national policy levels (berulo is a name that reflects these qualities - colours need to reflect amythyst in some way). I also need a design that translates from a business card as 1 medium of interaction to a template that can work in word/powerpoint etc to support both stationery as well as a digital strategy across multiple channels (fb/twit/etc)There is no slogan/tag line for the company and their is no logo. I was looking to just leverage the name - have currently played around with various fonts (ending up with cuisine - all lowercase).

Industry/Entity Type

Adult

Contact Information for Business Card

name: berulo (all lowercase)Chairman: Andrew CrowMobile: +61 418 902 131Web: www.berulo.comemail: martin.pelly@berulo-example.com

Font styles to use
Script
Other font styles liked:
• cuisine

Colors
e34298
e667a6
33a6d7
aaaaaa

Requirements
Nice to have
• https://files.example-share.net/sh/qx7kw2hd91lzmnp/AAFr3tYbQeLp8VwZnKcDs2Hu?dl=0
• Link to the printwell templates used to begin this process....the one with the lines was about people intersecting (collaborating).....the organic shapes one more of a fluid feel of people coming together - the overall shape being largely spherical could represent a "global" feel.....anyway that is how I was thinking about these

```html
<!DOCTYPE html>
<html lang="en">
<head>
<meta charset="utf-8">
<title>berulo – Martin Pelly business card</title>
<link rel="stylesheet" href="https://fonts.googleapis.com/css2?family=Damion&family=Kaushan+Script&display=swap">
<style>
  :root {
    --card-grey: #aaaaaa;
    --amethyst: #9b59b6;
    --magenta: #e34298;
    --orchid: #e667a6;
    --sky: #33a6d7;
    --ink-white: #ffffff;
  }
  html, body {
    margin: 0;
    padding: 0;
    overflow: hidden;
    background: var(--card-grey);
  }
  .card {
    position: relative;
    width: 1200px;
    height: 740px;
    background: var(--card-grey);
    overflow: hidden;
    font-family: "Damion", cursive;
  }
  .world-map {
    position: absolute;
    left: -40px;
    top: 150px;
    width: 540px;
    height: 480px;
    background: radial-gradient(ellipse closest-side at 50% 50%,
      rgba(230,103,166,0.55) 0%,
      rgba(155,89,182,0.40) 45%,
      rgba(51,166,215,0.22) 75%,
      rgba(170,170,170,0) 100%);
  }
  .brand-name {
    position: absolute;
    left: 24px;
    top: 300px;
    margin: 0;
    font-size: 118px;
    line-height: 1;
    font-weight: 400;
    color: var(--ink-white);
  }
  .person {
    position: absolute;
    right: 76px;
    top: 70px;
    text-align: right;
  }
  .person-name {
    margin: 0;
    font-size: 118px;
    line-height: 1;
    font-weight: 400;
    color: var(--ink-white);
  }
  .person-role {
    margin: 6px 0 0;
    font-family: "Kaushan Script", cursive;
    font-size: 50px;
    line-height: 1;
    color: var(--magenta);
  }
  .contacts {
    position: absolute;
    left: 682px;
    top: 488px;
    margin: 0;
    padding: 0;
    list-style: none;
  }
  .contact-item {
    display: flex;
    align-items: center;
    height: 46px;
    font-size: 30px;
    color: var(--ink-white);
  }
  .contact-icon {
    width: 30px;
    height: 30px;
    margin-right: 32px;
    fill: var(--amethyst);
    stroke: var(--amethyst);
  }
</style>
</head>
<body>
<main class="card">
  <div class="world-map" role="img" aria-label="Faint world map decoration in amethyst, pink and blue tones"></div>
  <p class="brand-name">berulo</p>

  <header class="person">
    <h1 class="person-name">Martin Pelly</h1>
    <p class="person-role">Chairman</p>
  </header>

  <ul class="contacts">
    <li class="contact-item">
      <svg class="contact-icon" viewBox="0 0 30 30" aria-hidden="true">
        <path stroke="none" d="M3 9c0-3 5-5 12-5s12 2 12 5v3h-6V9H9v3H3z"/>
        <path stroke="none" d="M8 13h14l4 11H4z"/>
        <circle cx="15" cy="18" r="3" fill="#aaaaaa" stroke="none"/>
      </svg>
      <span>+61 427 315 086</span>
    </li>
    <li class="contact-item">
      <svg class="contact-icon" viewBox="0 0 30 30" aria-hidden="true">
        <rect x="2" y="6" width="26" height="18" fill="none" stroke-width="2.5"/>
        <path d="M2 6l13 11 13-11M2 24l10-9M28 24l-10-9" fill="none" stroke-width="2"/>
      </svg>
      <span>martin.pelly@berulo-example.com</span>
    </li>
    <li class="contact-item">
      <svg class="contact-icon" viewBox="0 0 30 30" aria-hidden="true">
        <g fill="none" stroke-width="2">
          <circle cx="15" cy="15" r="12"/>
          <ellipse cx="15" cy="15" rx="5" ry="12"/>
          <path d="M3 15h24M5 9h20M5 21h20"/>
        </g>
      </svg>
      <span>www.berulo-example.com</span>
    </li>
  </ul>
</main>
</body>
</html>
```